Reliable and clean label for a natural product!

We would like to have a label design for our CBD SOFT GEL CAPSULES . We are a business family and believe in the power of natural healing. In this label we would like to show a reliable, natural and feminine product mainly.

Font styles to use
Serif
Sans Serif

Colors

Designer to choose colors to be used in the design.

```html
<!DOCTYPE html>
<html lang="en">
<head>
<meta charset="UTF-8">
<title>Solira CBD – Soft Gel Capsules Label</title>
<link rel="stylesheet" href="https://fonts.googleapis.com/css2?family=Montserrat:wght@400;500&family=Oswald:wght@600&family=Allura&family=Quicksand:wght@500&display=swap">
<style>
  :root {
    --page-bg: #ffffff;
    --label-white: #fbfbfb;
    --sand-light: #ede2d8;
    --sand-dark: #c4b1a0;
    --tan-accent: #d3b9a3;
    --ink: #3a3a3a;
    --ink-soft: #4a4a4a;
    --frame-line: #ffffff;
  }
  html, body {
    margin: 0;
    width: 1200px;
    height: 1200px;
    overflow: hidden;
    background: var(--page-bg);
  }
  .canvas {
    position: relative;
    width: 1200px;
    height: 1200px;
  }
  .label {
    position: absolute;
    left: 180px;
    top: 100px;
    width: 840px;
    height: 1000px;
    background: var(--label-white);
    box-shadow: 0 2px 18px rgba(0,0,0,0.06);
    overflow: hidden;
  }
  .label__lower {
    position: absolute;
    left: 0;
    top: 369px;
    width: 100%;
    height: 631px;
    background: linear-gradient(90deg, var(--sand-light) 0%, #d9c9ba 50%, var(--sand-dark) 100%);
  }
  .centered {
    position: absolute;
    left: 50%;
    transform: translate(-50%, -50%);
    white-space: nowrap;
    margin: 0;
  }
  .tagline {
    top: 59px;
    font-family: "Montserrat", sans-serif;
    font-weight: 400;
    font-size: 27px;
    letter-spacing: 0.5px;
    color: var(--tan-accent);
  }
  .brand-name {
    top: 189px;
    font-family: "Montserrat", sans-serif;
    font-weight: 500;
    font-size: 58px;
    letter-spacing: 1px;
    color: var(--ink);
  }
  .brand-circle {
    position: absolute;
    left: 320px;
    top: 239px;
    width: 200px;
    height: 200px;
  }
  .product-title {
    top: 537px;
    font-family: "Oswald", sans-serif;
    font-weight: 600;
    font-size: 82px;
    letter-spacing: 1px;
    background: linear-gradient(90deg, #6a6a6a, #2e2e2e 50%, #5a5a5a);
    -webkit-background-clip: text;
    background-clip: text;
    color: transparent;
  }
  .product-subtitle {
    top: 652px;
    font-family: "Allura", cursive;
    font-size: 104px;
    color: var(--ink);
  }
  .spectrum-badge {
    top: 766px;
    width: 408px;
    height: 66px;
    box-sizing: border-box;
    border: 2px solid var(--frame-line);
    display: flex;
    align-items: center;
    justify-content: center;
    font-family: "Montserrat", sans-serif;
    font-weight: 400;
    font-size: 36px;
    letter-spacing: 2px;
    color: var(--ink);
  }
  .dosage {
    top: 854px;
    font-family: "Quicksand", sans-serif;
    font-weight: 500;
    font-size: 38px;
    letter-spacing: 1.5px;
    color: var(--ink-soft);
  }
  .divider {
    top: 897px;
    width: 344px;
    height: 3px;
    border-radius: 50%;
    background: var(--ink);
  }
  .count {
    top: 950px;
    font-family: "Montserrat", sans-serif;
    font-weight: 400;
    font-size: 34px;
    letter-spacing: 2px;
    color: var(--ink);
  }
</style>
</head>
<body>
  <main class="canvas">
    <section class="label">
      <div class="label__lower"></div>

      <p class="centered tagline">RESTORATIVE SUPPLEMENT</p>
      <h1 class="centered brand-name">SOLIRA CBD</h1>

      <svg class="brand-circle" viewBox="0 0 200 200" aria-hidden="true">
        <circle cx="100" cy="100" r="97" fill="#fbfbfb" stroke="#d3b9a3" stroke-width="4"/>
      </svg>

      <h2 class="centered product-title">CBD SOFT GELS</h2>
      <p class="centered product-subtitle">Capsules</p>
      <div class="centered spectrum-badge">FULL SPECTRUM</div>
      <p class="centered dosage">25mg cbd per capsule</p>
      <div class="centered divider"></div>
      <p class="centered count">30 CAPSULES</p>
    </section>
  </main>
</body>
</html>
```